Simple, 1-Page Project - Life-saving AED Devices

We recently kicked off a project to bring all geographic location records for automatic emergency defibrillators (AEDs) in the State of New York online (instead of kept in paper in drawers). This hope is that is will ultimately save thousands of lives, as 9-1-1 operators will be able to quickly direct civilians to the nearest AED to bring to people suffering a cardiac event (e.g., a heart attack).

This page will be used to describe this effort, our progress thus far and how far we have left to go.

I am looking for a 1-page design - coded for both a responsive version for mobile devices and a traditional version - that would ***ideally*** plug into my existing WordPress site (https://qv-lmt.org), but it's not a requirement.

Target Market(s)

General public (non-physicians/non-EMTs)

Requirements
Must have
• - Our logo (please note, our logo is the Birchfield Vale Chapter logo...attached)
Nice to have
• - Would be wonderful to have an area with a clickable map showing where the participating regions are - which, once clicked, will take to you their specific sites. Regions are large chunks of land encompassing multiple towns, NOT a singular, specific place A nice-looking Google Map, a la Plumtail Grids (https://plumtailgrids.com/) would be cool if this were possible..
• - If you need a headline or page title, you can use: "Bringing AEDs in New York Online"
• - Would be nice if the design incorporated the color scheme of our brand (see attachment) and/or our main website: https://qv-lmt.org/
• - Would be nice to have some AED imagery - I attached some common symbols seen in AED advertising for inspiration
Should not have
• - This is a serious topic, so the design should be respectful and not too silly/cartoonish
• - Stock images, if chosen, should be thoughtful and classy

```html
<!DOCTYPE html>
<html lang="en">
<head>
<meta charset="utf-8">
<title>Bringing AEDs in New York Online</title>
<link href="https://fonts.googleapis.com/css2?family=Lato:ital,wght@0,400;0,700;0,900;1,400&display=swap" rel="stylesheet">
<style>
:root{
  --navy:#0c3a74;
  --navy-deep:#0a2d62;
  --orange:#f0731f;
  --ink:#3a3a3a;
  --text:#555;
  --grey-bg:#f1f1f1;
  --white:#fff;
}
*{box-sizing:border-box;margin:0;padding:0}
html,body{width:1200px;height:3947px;overflow:hidden}
body{font-family:'Lato',sans-serif;color:var(--text);background:var(--white);position:relative}
.abs{position:absolute}
.btn{position:absolute;display:flex;align-items:center;justify-content:center;color:var(--white);font-weight:700;font-size:16px;letter-spacing:.3px;text-decoration:none}
.btn--navy{background:var(--navy)}
.btn--orange{background:var(--orange)}
.section-title{position:absolute;left:0;width:1200px;text-align:center;font-weight:700;font-size:29px;color:var(--ink);letter-spacing:.3px}
.media{position:absolute}

/* header */
.site-header{position:absolute;left:0;top:0;width:1200px;height:112px}
.brand{position:absolute;left:75px;top:22px;display:flex;align-items:center;gap:12px}
.brand__mark{width:66px;height:66px;border-radius:50%;background:var(--navy)}
.brand__name{font-weight:700;font-size:19px;line-height:21px;color:var(--navy);text-transform:uppercase}
.contact-bar{position:absolute;right:75px;top:36px;display:flex;align-items:center;gap:8px;font-size:18px;color:var(--navy);font-weight:700}
.contact-bar .ic{width:38px;height:38px;border:1.5px solid #bbb;border-radius:50%;display:flex;align-items:center;justify-content:center}
.contact-bar .email{font-weight:400;font-size:17px}
.main-nav{position:absolute;left:0;top:112px;width:1200px;height:49px;background:var(--navy);display:flex;justify-content:center;align-items:center;gap:44px}
.main-nav a{color:var(--white);font-weight:700;font-size:14px;text-decoration:none}

/* hero */
.hero{position:absolute;left:0;top:161px;width:1200px;height:662px}
.hero__title{position:absolute;left:73px;top:165px;font-weight:900;font-size:40px;line-height:44px;color:#1c1c1c}
.hero__dots{position:absolute;left:75px;top:496px;display:flex;gap:11px}
.hero__dots span{width:9px;height:9px;background:#8a8f96}
.hero__dots span:first-child{background:var(--white)}

p.body{font-size:14.5px;line-height:27.5px}

/* band */
.aed-band{position:absolute;left:0;top:1221px;width:1200px;height:373px;background:radial-gradient(ellipse at 25% 55%,#1b6bb0 0%,#0f4a8c 40%,var(--navy) 80%)}
.aed-band h2{position:absolute;left:526px;top:46px;font-size:29px;font-weight:700;color:var(--white)}
.aed-band p{position:absolute;left:526px;top:94px;width:545px;color:#e8eef6}

/* testimonials */
.testimonials{position:absolute;left:0;top:2176px;width:1200px;height:445px;background:var(--grey-bg)}
.t-card{position:absolute;top:134px;width:300px;text-align:center}
.t-card .stars{color:var(--orange);font-size:15px;letter-spacing:3px}
.t-card q{display:block;width:270px;margin:6px auto 0;font-style:italic;font-size:14px;line-height:26px;color:var(--text);quotes:"\201C" ""}
.t-card .avatar{width:68px;height:68px;margin:29px auto 0;background:linear-gradient(#d9d9d9,#9a9a9a)}
.t-card .name{margin-top:18px;font-weight:700;font-size:14.5px;color:var(--navy)}
.arrow{position:absolute;top:212px;font-size:28px;color:#222;font-weight:700}

/* blog */
.post{position:absolute;top:2748px;width:330px;text-align:center}
.post .thumb{height:187px}
.post h3{margin-top:32px;font-size:16px;font-weight:700;color:var(--navy)}
.post p{margin-top:8px;font-size:14px;line-height:25px}
.post time{display:block;margin-top:6px;font-weight:700;font-size:14px;color:#333}
.pager{position:absolute;left:551px;top:3126px;display:flex;gap:10px}
.pager span{width:27px;height:4px;background:#888}
.pager span:first-child{background:var(--navy)}

/* footer */
.site-footer{position:absolute;left:0;top:3203px;width:1200px;height:744px}
.footer__seal{position:absolute;left:548px;top:32px;width:106px;height:106px;border-radius:50%;background:var(--white);border:6px solid var(--navy-deep);box-shadow:0 0 0 3px var(--white)}
.site-footer h2{position:absolute;left:0;width:1200px;top:182px;text-align:center;color:var(--white);font-size:29px;font-weight:700}
.site-footer .lead{position:absolute;left:200px;width:800px;top:248px;text-align:center;color:#e3e9f3;font-size:15px;line-height:26px}
.field{position:absolute;background:var(--white);font-size:14px;color:#444;padding:14px 12px}
.contact-info{position:absolute;left:817px;top:333px;color:#e7edf6}
.contact-info h3{font-size:22px;font-weight:700;color:var(--white)}
.contact-info h4{margin-top:14px;font-size:14px;font-weight:700;color:var(--white)}
.contact-info li{list-style:none;font-size:14px;line-height:22px;margin-top:9px;display:flex;gap:8px}
.socials{position:absolute;left:817px;top:558px;display:flex;gap:14px}
.socials a{color:var(--white);font-weight:700;font-size:14px;text-decoration:none}
.footer__rule{position:absolute;left:75px;width:1050px;top:659px;height:1px;background:#5b74a0}
.copyright{position:absolute;left:0;width:1200px;top:698px;text-align:center;color:#dbe3f0;font-size:12.5px}
</style>
</head>
<body>

<header class="site-header">
  <div class="brand">
    <div class="brand__mark"></div>
    <div class="brand__name">Birchfield Vale<br>Heart College</div>
  </div>
  <div class="contact-bar">
    <span class="ic"><svg width="14" height="14" viewBox="0 0 24 24"><path fill="#0c3a74" d="M6.6 10.8c1.4 2.8 3.8 5.1 6.6 6.6l2.2-2.2c.3-.3.7-.4 1-.2 1.1.4 2.3.6 3.6.6.6 0 1 .4 1 1V20c0 .6-.4 1-1 1C10.6 21 3 13.4 3 4c0-.6.4-1 1-1h3.5c.6 0 1 .4 1 1 0 1.3.2 2.5.6 3.6.1.3 0 .7-.2 1z"/></svg></span>
    <span>1-800-555-0142</span>
    <span class="ic"><svg width="14" height="12" viewBox="0 0 24 20"><path fill="#0c3a74" d="M2 2h20v16H2z"/><path fill="none" stroke="#fff" stroke-width="2" d="M2 3l10 8 10-8"/></svg></span>
    <span class="email">hello@birchfieldvale.org</span>
  </div>
</header>

<nav class="main-nav">
  <a href="#">HOME</a><a href="#">ABOUT US</a><a href="#">ABOUT AED</a><a href="#">HOW IT WORKS</a><a href="#">BLOG</a><a href="#">REVIEWS</a><a href="#">CONTACT US</a>
</nav>

<section class="hero">
  <svg class="abs" width="1200" height="662" style="left:0;top:0" role="img" aria-label="Photo of a hand pressing the button of a yellow and red AED device with a heartbeat line">
    <defs>
      <linearGradient id="heroBg" x1="0" y1="0" x2="1" y2="1">
        <stop offset="0" stop-color="#b9c9dc"/><stop offset=".45" stop-color="#c9c4a8"/><stop offset=".75" stop-color="#eeb64a"/><stop offset="1" stop-color="#d9424a"/>
      </linearGradient>
    </defs>
    <polygon points="0,0 1200,0 1200,558 598,662 0,575" fill="url(#heroBg)"/>
  </svg>
  <h1 class="hero__title">BRINGING AEDs<br>IN NEW YORK ONLINE</h1>
  <a class="btn btn--navy" style="left:75px;top:285px;width:180px;height:57px" href="#">READ MORE</a>
  <div class="hero__dots"><span></span><span></span><span></span><span></span></div>
</section>

<section class="welcome">
  <h2 class="abs" style="left:75px;top:884px;font-size:29px;font-weight:700;color:var(--ink)">WELCOME TO OUR WEBSITE</h2>
  <p class="abs body" style="left:75px;top:934px;width:545px">Lorem ipsum dolor sit amet, consectetur adipiscing elit. Integer in nisi eget lacus laoreet finibus ut at ex. Suspendisse non accumsan elit. Nullam ut aliquam nisi. Suspendisse egestas pretium posuere. Nulla sollicitudin urna non luctus tempor. Fusce ac odio id magna &nbsp;vestibulum commodo. Sed vitae lacus pharetra, ornare purus a, sagittis nisl.</p>
  <a class="btn btn--orange" style="left:75px;top:1102px;width:181px;height:57px" href="#">READ MORE</a>
  <div class="media" style="left:676px;top:890px;width:451px;height:269px;background:linear-gradient(90deg,#8fcf3a 0%,#a6d65a 42%,#d9c1b4 62%,#c98f80 100%)" role="img" aria-label="Green AED device beside open hands holding a red heart"></div>
</section>

<section class="aed-band">
  <div class="media" style="left:100px;top:51px;width:352px;height:284px;background:linear-gradient(90deg,#f07a2a 0%,#f08a3a 48%,#3d8a4e 55%,#2f7340 100%);border-radius:8px" role="img" aria-label="Orange defibrillator unit with green emergency cabinet"></div>
  <h2>AUTOMATIC EMERGENCY DEFIBRILLATORS</h2>
  <p class="body">Lorem ipsum dolor sit amet, consectetur adipiscing elit. Integer in nisi eget lacus laoreet finibus ut at ex. Suspendisse non accumsan elit. Nullam ut aliquam nisi. Suspendisse egestas pretium posuere. Nulla sollicitudin urna non luctus tempor. Fusce ac odio id magna &nbsp;vestibulum commodo. Sed vitae lacus pharetra, ornare purus a, sagittis nisl.</p>
  <a class="btn btn--orange" style="left:526px;top:264px;width:181px;height:57px" href="#">READ MORE</a>
</section>

<section class="locations">
  <h2 class="section-title" style="top:1646px">LOCATIONS RECORDS</h2>
  <div class="media" style="left:75px;top:1703px;width:512px;height:418px;background:linear-gradient(135deg,#ebebe8,#dfe3d8)" role="img" aria-label="Grey road map of a participating region with a location marker">
    <svg class="abs" style="left:237px;top:180px" width="36" height="52" viewBox="0 0 36 52"><path d="M18 0C8 0 0 8 0 18c0 13 18 30 18 30s18-17 18-30C36 8 28 0 18 0z" fill="#e8541e"/><circle cx="18" cy="18" r="7" fill="#fff"/></svg>
  </div>
  <div class="media" style="left:613px;top:1703px;width:514px;height:418px;background:linear-gradient(135deg,#dde3d6,#c9d3de)" role="img" aria-label="Grey road map of a second participating region with a location marker">
    <svg class="abs" style="left:239px;top:168px" width="36" height="52" viewBox="0 0 36 52"><path d="M18 0C8 0 0 8 0 18c0 13 18 30 18 30s18-17 18-30C36 8 28 0 18 0z" fill="#e8541e"/><circle cx="18" cy="18" r="7" fill="#fff"/></svg>
  </div>
</section>

<section class="testimonials">
  <h2 class="section-title" style="top:54px">TESTIMONIALS</h2>
  <span class="arrow" style="left:46px">&#8249;</span>
  <span class="arrow" style="left:1138px">&#8250;</span>
  <div class="t-card" style="left:89px"><div class="stars">★★★★★</div><q>Lorem ipsum dolor sit amet, consectetur adipiscing elit. Integer in nisi eget lacus laoreet finibus ut at ex uspendisse non accumsan elit...:</q><div class="avatar" role="img" aria-label="Portrait of reviewer"></div><div class="name">Name Heading</div></div>
  <div class="t-card" style="left:451px"><div class="stars">★★★★★</div><q>Lorem ipsum dolor sit amet, consectetur adipiscing elit. Integer in nisi eget lacus laoreet finibus ut at ex uspendisse non accumsan elit...:</q><div class="avatar" role="img" aria-label="Portrait of reviewer"></div><div class="name">Name Heading</div></div>
  <div class="t-card" style="left:811px"><div class="stars">★★★★★</div><q>Lorem ipsum dolor sit amet, consectetur adipiscing elit. Integer in nisi eget lacus laoreet finibus ut at ex uspendisse non accumsan elit...:</q><div class="avatar" role="img" aria-label="Portrait of reviewer"></div><div class="name">Name Heading</div></div>
</section>

<section class="blog">
  <h2 class="section-title" style="top:2676px">BLOG POSTS</h2>
  <article class="post" style="left:75px"><div class="thumb" role="img" aria-label="Yellow AED with electrode pads on a grey surface" style="background:linear-gradient(120deg,#8d9399,#b9a66a 65%,#d4a437)"></div><h3>NUNC DAPIBUS IPSUM EGET</h3><p>Lorem ipsum dolor sit amet, consectetur<br>adipiscing elit eget lacus...</p><time>Jun16, 2019</time></article>
  <article class="post" style="left:435px"><div class="thumb" role="img" aria-label="Red AED case being opened" style="background:linear-gradient(120deg,#c9a99a,#d8323a 45%,#b01f2a)"></div><h3>NUNC DAPIBUS IPSUM EGET</h3><p>Lorem ipsum dolor sit amet, consectetur<br>adipiscing elit eget lacus...</p><time>Jun16, 2019</time></article>
  <article class="post" style="left:796px"><div class="thumb" role="img" aria-label="CPR training class with AED on the floor" style="background:linear-gradient(120deg,#8f9677,#c4b299 55%,#e3b13c)"></div><h3>NUNC DAPIBUS IPSUM EGET</h3><p>Lorem ipsum dolor sit amet, consectetur<br>adipiscing elit eget lacus...</p><time>Jun16, 2019</time></article>
  <div class="pager"><span></span><span></span><span></span></div>
</section>

<footer class="site-footer">
  <svg class="abs" style="left:0;top:0" width="1200" height="744"><polygon points="0,0 601,80 1200,0 1200,744 0,744" fill="#0a2d62"/></svg>
  <div class="footer__seal"></div>
  <h2>CONTACT US</h2>
  <p class="lead">Lorem ipsum dolor sit amet, consectetur adipiscing elit. Integer in nisi eget lacus laoreet finibus ut at ex.<br>Suspendisse non accumsan elit.</p>
  <div class="field" style="left:75px;top:337px;width:330px;height:47px">Name</div>
  <div class="field" style="left:435px;top:337px;width:330px;height:47px">Email Address</div>
  <div class="field" style="left:75px;top:397px;width:690px;height:132px">Message</div>
  <a class="btn btn--orange" style="left:77px;top:546px;width:138px;height:57px" href="#">SEND</a>
  <div class="contact-info">
    <h3>CONTACT INFO</h3>
    <h4>AED DEVICES</h4>
    <ul>
      <li><span>&#9679;</span><span>42 Larkspur Lane, Hollowmere,<br>HM7 2QT</span></li>
      <li><span>&#9742;</span><span>1-800-555-0143</span></li>
      <li><span>&#9993;</span><span>hello@birchfieldvale.org</span></li>
    </ul>
  </div>
  <div class="socials"><a href="#">Share</a><a href="#">Post</a><a href="#">Photo</a><a href="#">Link</a><a href="#">Video</a></div>
  <div class="footer__rule"></div>
  <p class="copyright">Copyright © 2019. Company Name. All Right Reserved</p>
</footer>

</body>
</html>
```